Salon and Spa Distributor Business Card

Need a business card. We are are distributor in the salon and spa industry. We identify with natural beauty. Need a card with:
Company Name: Petal Quarry"
Title: "President & CEO"
Address
Company Phone number
email
website
Tag Line:" The Professional Salon Source"

Industry/Entity Type

Business

Contact Information for Business Card

Name: Dov Strommen
Title: "President & CEO"
Address: 31 Harlow Ln, Bexmoor, NJ 07813
Company Phone number: 800-463-5918
email: dovstrommen@petalquarry.example
website: www.petalquarry.example

Requirements
Should not have
• No black backgrounds

```html
<!DOCTYPE html>
<html lang="en">
<head>
<meta charset="utf-8">
<title>Petal Quarry — Business Card</title>
<link rel="stylesheet" href="https://fonts.googleapis.com/css2?family=Source+Sans+3:ital,wght@0,400;0,600;0,700;1,400;1,600&display=swap">
<style>
  :root {
    --page-bg: #dcdfdd;
    --card-bg: #eef1ef;
    --card-edge: #d2d8d4;
    --brand-green: #2f6e2c;
    --leaf-green: #3f8f36;
    --leaf-light: #6bb85a;
    --leaf-pale: #cfe3ca;
    --text-dark: #2b2f2c;
    --text-muted: #555b57;
  }
  * { box-sizing: border-box; margin: 0; padding: 0; }
  html, body {
    width: 1200px;
    height: 969px;
    overflow: hidden;
    background: var(--page-bg);
    font-family: "Source Sans 3", "Helvetica Neue", Arial, sans-serif;
  }
  .business-card {
    position: absolute;
    left: 100px;
    top: 201px;
    width: 1000px;
    height: 567px;
    background: var(--card-bg);
    border: 1px solid var(--card-edge);
    border-radius: 30px;
    overflow: hidden;
  }
  .edge-dot {
    position: absolute;
    left: -17px;
    top: 81px;
    width: 34px;
    height: 34px;
    border-radius: 50%;
    background: var(--brand-green);
  }
  .contact-block {
    position: absolute;
    left: 65px;
    top: 62px;
    width: 480px;
    color: var(--text-dark);
  }
  .company-name {
    font-size: 33px;
    font-weight: 700;
    color: var(--brand-green);
    line-height: 40px;
  }
  .job-title {
    font-size: 25px;
    color: var(--text-muted);
    line-height: 32px;
  }
  .address {
    margin-top: 40px;
    font-size: 25px;
    line-height: 38px;
    font-style: normal;
  }
  .contact-list {
    list-style: none;
    margin-top: 8px;
    font-size: 25px;
    line-height: 38px;
  }
  .contact-list li {
    display: flex;
    align-items: center;
    gap: 12px;
    white-space: nowrap;
  }
  .contact-list svg {
    width: 22px;
    height: 22px;
    fill: var(--brand-green);
    flex: none;
  }
  .wordmark {
    position: absolute;
    left: 62px;
    top: 400px;
    font-size: 58px;
    font-weight: 400;
    color: var(--leaf-green);
    letter-spacing: -0.5px;
    line-height: 66px;
  }
  .tagline {
    position: absolute;
    left: 65px;
    top: 470px;
    font-size: 27px;
    font-style: italic;
    font-weight: 600;
    color: var(--text-dark);
  }
  .brand-illustration {
    position: absolute;
    left: 590px;
    top: 24px;
    width: 380px;
    height: 520px;
    border-radius: 50%;
    background: radial-gradient(ellipse at 50% 45%, var(--leaf-light) 0%, var(--leaf-green) 55%, var(--leaf-pale) 100%);
  }
</style>
</head>
<body>
  <section class="business-card">
    <span class="edge-dot"></span>

    <div class="contact-block">
      <h1 class="company-name">Petal Quarry</h1>
      <p class="job-title">President &amp; CEO</p>
      <address class="address">31 Harlow Ln<br>Bexmoor, NJ 07813</address>
      <ul class="contact-list">
        <li>
          <svg viewBox="0 0 24 24" aria-hidden="true"><path d="M6.6 10.8a15.2 15.2 0 0 0 6.6 6.6l2.2-2.2a1 1 0 0 1 1-.25 11.4 11.4 0 0 0 3.6.57 1 1 0 0 1 1 1V20a1 1 0 0 1-1 1A17 17 0 0 1 3 4a1 1 0 0 1 1-1h3.5a1 1 0 0 1 1 1c0 1.25.2 2.45.57 3.570a1 1 0 0 1-.25 1z"/></svg>
          <span>800-463-5918</span>
        </li>
        <li>
          <svg viewBox="0 0 24 24" aria-hidden="true"><path d="M2 5h20v14H2z M3.5 6.5 12 12.5l8.5-6H3.5z" fill-rule="evenodd"/></svg>
          <span>dovstrommen@petalquarry.example</span>
        </li>
        <li>
          <svg viewBox="0 0 24 24" aria-hidden="true"><path d="M12 2a10 10 0 1 0 0 20 10 10 0 0 0 0-20zm0 2c1.2 0 2.6 2.3 3 6H9c.4-3.700 1.800-6 3-6zM4.1 10h3a17 17 0 0 1 .6-4.7A8 8 0 0 0 4.1 10zm12.8 0h3a8 8 0 0 0-3.6-4.7c.4 1.3.6 2.9.6 4.7zM4.1 14a8 8 0 0 0 3.6 4.7 17 17 0 0 1-.6-4.7zm4.9 0c.4 3.7 1.8 6 3 6s2.6-2.3 3-6zm7.9 0c0 1.8-.2 3.4-.6 4.7a8 8 0 0 0 3.6-4.7z"/></svg>
          <span>www.petalquarry.example</span>
        </li>
      </ul>
    </div>

    <p class="wordmark">PetalQuarry</p>
    <p class="tagline">The Professional Salon Source</p>

    <div class="brand-illustration" role="img" aria-label="Green illustration of a woman's profile with flowing hair and leaves"></div>
  </section>
</body>
</html>
```